Restyle corporate identity (+ logo) for a road construction company

We need a new logo and stationary design for our company VARNOK path. VARNOK path® increases the road base strength, while reducing major costs and time of road construction. Attached some examples of the current design.

Our wishes for the new logo:
- Business look
- Style sheet
- Modern

More information: www.varnokpath.example
Updates

Target Market(s)

Government

Industry/Entity Type

Construction

Requirements
Must have
• Logo (with road sign) + text

```html
<!DOCTYPE html>
<html lang="en">
<head>
<meta charset="utf-8">
<title>VARNOK path – Business Card</title>
<link rel="stylesheet" href="https://fonts.googleapis.com/css2?family=Source+Sans+3:wght@400;600&display=swap">
<style>
  :root {
    --backdrop: #8f9091;
    --brand-blue: #0b79e0;
    --card-white: #eeeeef;
    --text-on-blue: #f2f6fb;
    --text-soft: #dce9f8;
    --divider: rgba(255,255,255,0.55);
    --logo-blue: #1e84e6;
  }
  * { margin: 0; padding: 0; box-sizing: border-box; }
  html, body { width: 1105px; height: 1200px; overflow: hidden; }
  body {
    background: var(--backdrop);
    font-family: "Source Sans 3", "Segoe UI", sans-serif;
    position: relative;
  }
  .card {
    position: absolute;
    left: 182px;
    width: 748px;
    height: 427px;
  }
  .card--front { top: 119px; background: var(--brand-blue); }
  .card--back  { top: 635px; background: var(--card-white); }

  .front-brand {
    position: absolute;
    left: 101px; top: 98px;
    width: 249px; height: 247px;
    display: flex; align-items: center; justify-content: center;
    text-align: center;
    color: var(--text-on-blue);
    font-weight: 600;
    font-size: 44px;
    line-height: 1.05;
  }
  .divider {
    position: absolute;
    left: 396px; top: 98px;
    width: 1px; height: 269px;
    background: var(--divider);
  }
  .details {
    position: absolute;
    left: 435px; top: 96px;
    color: var(--text-soft);
  }
  .person-name {
    font-weight: 600;
    font-size: 25px;
    letter-spacing: 0.5px;
    color: var(--text-on-blue);
    line-height: 30px;
  }
  .person-role { font-size: 19px; line-height: 24px; }
  .address { margin-top: 18px; font-size: 19px; line-height: 26px; font-style: normal; }
  .contact { list-style: none; margin-top: 14px; }
  .contact li {
    display: flex; align-items: center; gap: 10px;
    font-size: 19px; line-height: 28.5px;
  }
  .contact svg { width: 16px; height: 16px; fill: var(--text-soft); flex: none; }

  .back-brand {
    position: absolute;
    inset: 0;
    display: flex; align-items: center; justify-content: center; gap: 16px;
  }
  .back-brand .mark-square {
    width: 72px; height: 72px;
    background: var(--logo-blue);
    border-radius: 10px;
  }
  .back-brand .brand-name {
    color: var(--logo-blue);
    font-weight: 600;
    font-size: 56px;
    letter-spacing: 1px;
  }
</style>
</head>
<body>
  <section class="card card--front">
    <div class="front-brand">VARNOK<br>path</div>
    <div class="divider"></div>
    <div class="details">
      <p class="person-name">MAREN HOLT</p>
      <p class="person-role">CEO/Founder</p>
      <address class="address">Lindenkade 58<br>3011 KP Rotterdam<br>The Netherlands</address>
      <ul class="contact">
        <li>
          <svg viewBox="0 0 16 16" aria-hidden="true"><path d="M3.6 1.2l2.3 2.6-1.3 2c.9 1.9 2.4 3.4 4.2 4.3l2-1.3 2.6 2.3-1.4 2.4C6.9 13.9 2.1 9.1 1.3 3.5z"/></svg>
          010 555 0147
        </li>
        <li>
          <svg viewBox="0 0 16 16" aria-hidden="true"><path d="M1 3.5h14v9H1z M1.6 4l6.4 4.8L14.4 4" fill="none" stroke="currentColor"/><path d="M1 3h14v1.2L8 9 1 4.2z M1 5.5l4.5 3.2L1 12.5z M15 5.5l-4.5 3.2 4.5 3.8z M6.3 9.3L8 10.5l1.7-1.2L15 13H1z"/></svg>
          info@varnokpath.example
        </li>
        <li>
          <svg viewBox="0 0 16 16" aria-hidden="true"><circle cx="8" cy="8" r="7"/><path d="M4.5 4.5c1.5.4 2 1.5 1.5 2.6-.5 1 .6 1.8 1.5 2.2.6 1.2-.2 2.4-.6 3.5M9.5 2.5c-.3 1.2.8 1.8 1.8 1.7 1 .4 1.2 1.6 2.2 2" fill="none" stroke="var(--brand-blue)" stroke-width="1.2"/></svg>
          www.varnokpath.example
        </li>
      </ul>
    </div>
  </section>

  <section class="card card--back">
    <div class="back-brand">
      <span class="mark-square"></span>
      <span class="brand-name">VARNOK path</span>
    </div>
  </section>
</body>
</html>
```